UX - Need some screens design for a Skill Assessment Application

I am building an app to carry out skill assessments. Depending on how the assessment is configured, it may have one or more parts
1. Question based assessment (Multiple Choice, True False, Fill in the blanks"
2. Endorsement by two colleagues - A screen that allows user to pick colleagues based on search and shows the status of pending requests
3. A written submission - a page that explains the format of the submission and a file upload
As each assessment can be configured with or without any of the steps, the assessment UI must be such that these areas get hidden/displayed based on configuration.
Colour codes to be used can be #0e78bb and #ffffff
There will also be a start screen (instructions) and an end screen (results)
Target Market(s)
Enterprise software
Number of Pages Required
4 page

```html
<!DOCTYPE html>
<html lang="en">
<head>
<meta charset="utf-8">
<title>Application Design Capabilities – Endorsement</title>
<link rel="stylesheet" href="https://fonts.googleapis.com/css2?family=Inter:wght@400;500;600;700&display=swap">
<style>
  :root{
    --brand:#0a55a8;
    --primary:#0e78bb;
    --white:#ffffff;
    --ink:#222a33;
    --muted:#555d66;
    --soft:#8a9199;
    --line:#dde1e6;
    --band:#f3f4f6;
    --head:#e8f4fb;
    --chip:#eef0f2;
    --link-faint:#8ccbec;
  }
  *{box-sizing:border-box;margin:0;padding:0}
  html,body{width:1200px;height:686px;overflow:hidden;background:var(--band);font-family:"Inter",Arial,sans-serif;color:var(--ink)}
  .page{width:1400px;height:800px;transform:scale(.857143);transform-origin:0 0;position:relative;background:var(--band)}
  .topbar{height:50px;background:var(--brand);display:flex;align-items:center;padding:0 63px 0 67px;color:var(--white)}
  .brand{display:flex;align-items:center;gap:14px;font-size:17px;font-weight:500}
  .brand-dot{width:25px;height:25px;border-radius:50%;background:var(--white)}
  .nav{margin-left:auto;display:flex;align-items:center;gap:24px;font-size:14px}
  .nav a{color:rgba(255,255,255,.82);text-decoration:none}
  .nav a.active{color:var(--white);font-weight:700}
  .user{display:flex;align-items:center;gap:8px;margin-left:-2px}
  .user-photo{width:32px;height:32px;border-radius:50%;background:linear-gradient(135deg,#6b4a3e,#c9a28a)}
  .hero{background:var(--white);height:113px;padding:28px 0 0 66px;border-bottom:1px solid var(--line)}
  .crumbs{display:flex;align-items:center;gap:8px;font-size:13px;color:var(--muted)}
  .crumbs a{color:var(--primary);text-decoration:none}
  .crumbs .back{margin-right:7px}
  .title{display:flex;align-items:center;gap:16px;margin:14px 0 0 37px;font-size:24px;font-weight:600}
  .filters{height:90px;border-bottom:1px solid var(--line);display:flex;align-items:flex-start;padding:17px 103px 0;gap:16px}
  .field label{display:block;font-size:11px;color:var(--muted);margin-bottom:8px}
  .box{height:36px;background:var(--white);border:1px solid var(--line);border-radius:3px;display:flex;align-items:center;justify-content:space-between;padding:0 12px 0 15px;font-size:13px}
  .box.placeholder{color:var(--soft)}
  .send{margin-left:auto;margin-top:30px;font-size:13px;color:var(--link-faint)}
  .card{position:absolute;left:103px;top:278px;width:1194px;height:482px;background:var(--white);border:1px solid var(--line);border-radius:3px;overflow:hidden}
  table{width:100%;border-collapse:collapse}
  th{background:var(--head);height:49px;text-align:left;font-size:14px;font-weight:600;color:var(--muted)}
  td{height:53px;border-top:1px solid var(--line);font-size:12px;color:var(--muted)}
  .c-check{width:47px;padding-left:19px}
  .check{width:16px;height:16px;border:1px solid #c8cdd3;border-radius:2px;background:var(--white)}
  .person{display:flex;align-items:center;gap:12px;font-size:14px;color:var(--ink);font-weight:500}
  th.c-name{width:224px}
  .avatar{width:32px;height:32px;border-radius:50%}
  .skills{display:flex;gap:5px}
  .chip{background:var(--chip);border-radius:11px;padding:4px 8px;font-size:11px;color:var(--muted)}
  th.c-skills{width:415px}
  th.c-role{width:225px}
  .company{color:var(--primary);font-weight:500}
  .add{width:57px;height:36px;border:1px solid var(--primary);border-radius:3px;color:var(--primary);font-size:13px;display:flex;align-items:center;justify-content:center}
  .pager{border-top:1px solid var(--line);height:64px;display:flex;align-items:center;justify-content:center;gap:16px;font-size:14px}
  .pg-btn{width:73px;height:36px;border:1px solid var(--line);border-radius:3px;color:#c3c8ce;font-size:13px;display:flex;align-items:center;justify-content:center}
  .pg-num{width:37px;height:36px;display:flex;align-items:center;justify-content:center;font-size:16px;color:var(--muted)}
  .pg-num.current{background:var(--primary);color:var(--white);border-radius:2px}
</style>
</head>
<body>
<div class="page">
  <header class="topbar">
    <div class="brand"><span class="brand-dot"></span>LogoPlaceholder</div>
    <nav class="nav">
      <a href="#">Assessments</a>
      <a href="#" class="active">Endorsement</a>
      <a href="#">Submissions</a>
      <a href="#">Results</a>
      <div class="user">
        <span class="user-photo" role="img" aria-label="User profile photo"></span>
        <svg width="12" height="8" viewBox="0 0 12 8"><path d="M1 1.5l5 5 5-5" stroke="#fff" stroke-width="1.8" fill="none"/></svg>
      </div>
    </nav>
  </header>

  <section class="hero">
    <div class="crumbs">
      <svg class="back" width="22" height="22" viewBox="0 0 22 22"><circle cx="11" cy="11" r="10" stroke="#0e78bb" stroke-width="1.8" fill="none"/><path d="M16 11H6.5M10.5 7L6.5 11l4 4" stroke="#0e78bb" stroke-width="1.8" fill="none" stroke-linecap="round" stroke-linejoin="round"/></svg>
      <a href="#">Endorsement</a><span>/</span><a href="#">New Endorsement Request</a><span>/</span><span>Application Design Capabilities</span>
    </div>
    <h1 class="title">
      <svg width="25" height="24" viewBox="0 0 25 24" fill="none" stroke="#555d66" stroke-width="1.5"><circle cx="12.5" cy="8" r="3.2"/><circle cx="5" cy="5.5" r="2.4"/><circle cx="20" cy="5.5" r="2.4"/><path d="M6.5 20c0-3.6 2.7-6.2 6-6.2s6 2.6 6 6.2M1 15c0-2.6 1.8-4.6 4-4.6M24 15c0-2.6-1.8-4.6-4-4.6"/></svg>
      Application Design Capabilities
    </h1>
  </section>

  <section class="filters">
    <div class="field" style="width:350px"><label>Choose Category</label>
      <div class="box">Application Design Capabilities (24)<svg width="12" height="8" viewBox="0 0 12 8"><path d="M1 1.5l5 5 5-5" stroke="#333" stroke-width="1.5" fill="none"/></svg></div></div>
    <div class="field" style="width:200px"><label>Effective Date</label>
      <div class="box">Select date<svg width="12" height="8" viewBox="0 0 12 8"><path d="M1 1.5l5 5 5-5" stroke="#333" stroke-width="1.5" fill="none"/></svg></div></div>
    <div class="field" style="width:334px"><label>Endorsement</label>
      <div class="box placeholder">Search<svg width="18" height="18" viewBox="0 0 18 18"><circle cx="7.5" cy="7.5" r="6" stroke="#777" stroke-width="1.5" fill="none"/><path d="M12 12l5 5" stroke="#777" stroke-width="1.5"/></svg></div></div>
    <div class="send">Send Endorsement Request</div>
  </section>

  <div class="card">
    <table>
      <thead><tr>
        <th class="c-check"><div class="check"></div></th>
        <th class="c-name">Endorsements</th>
        <th class="c-skills">Skill &amp; Expertise</th>
        <th class="c-role">Role</th>
        <th>Company</th>
        <th></th>
      </tr></thead>
      <tbody>
        <tr><td class="c-check"><div class="check"></div></td><td><div class="person"><span class="avatar" role="img" aria-label="Portrait of Mei Lan Zhou" style="background:#7a5a3c"></span>Mei Lan Zhou</div></td>
          <td><div class="skills"><span class="chip">UI</span><span class="chip">UX</span><span class="chip">Wireframe</span><span class="chip">Concept Design</span><span class="chip">Mockup</span></div></td>
          <td>Lantern Bay Industries Ltd.</td><td class="company">Lantern Bay Industries Ltd.</td><td><div class="add">Add</div></td></tr>
        <tr><td class="c-check"><div class="check"></div></td><td><div class="person"><span class="avatar" role="img" aria-label="Portrait of Harold Denton" style="background:#3b3a38"></span>Harold Denton</div></td>
          <td><div class="skills"><span class="chip">Concept Design</span><span class="chip">Mockup</span></div></td>
          <td>Brightpath Corp.</td><td class="company">Brightpath Corp.</td><td><div class="add">Add</div></td></tr>
        <tr><td class="c-check"><div class="check"></div></td><td><div class="person"><span class="avatar" role="img" aria-label="Portrait of Mark Tillman" style="background:#6d6a66"></span>Mark Tillman</div></td>
          <td><div class="skills"><span class="chip">UI</span><span class="chip">Design Analytic</span></div></td>
          <td>Brightpath Corp.</td><td class="company">Brightpath Corp.</td><td><div class="add">Add</div></td></tr>
        <tr><td class="c-check"><div class="check"></div></td><td><div class="person"><span class="avatar" role="img" aria-label="Portrait of Alina Kerr" style="background:#e2b98a"></span>Alina Kerr</div></td>
          <td><div class="skills"><span class="chip">Wireframe</span><span class="chip">Concept Design</span><span class="chip">Mockup</span></div></td>
          <td>Brightpath Corp.</td><td class="company">Brightpath Corp.</td><td><div class="add">Add</div></td></tr>
        <tr><td class="c-check"><div class="check"></div></td><td><div class="person"><span class="avatar" role="img" aria-label="Portrait of Rowan Marsh Jr." style="background:#8fc3d6"></span>Rowan Marsh Jr.</div></td>
          <td><div class="skills"><span class="chip">UX</span><span class="chip">Concept Design</span></div></td>
          <td>Brightpath Corp.</td><td class="company">Brightpath Corp.</td><td><div class="add">Add</div></td></tr>
        <tr><td class="c-check"><div class="check"></div></td><td><div class="person"><span class="avatar" role="img" aria-label="Portrait of Dewi R. Pratiwi" style="background:#4c5f7e"></span>Dewi R. Pratiwi</div></td>
          <td><div class="skills"><span class="chip">Design Analytic</span><span class="chip">Wireframe</span></div></td>
          <td>Kirana Studio</td><td class="company">Kirana Studio</td><td><div class="add">Add</div></td></tr>
        <tr><td class="c-check"><div class="check"></div></td><td><div class="person"><span class="avatar" role="img" aria-label="Portrait of Ronald Clayton" style="background:#cfc6bd"></span>Ronald Clayton</div></td>
          <td><div class="skills"><span class="chip">Wireframe</span><span class="chip">UX</span><span class="chip">Concept Design</span><span class="chip">UI</span></div></td>
          <td>Brightpath Corp.</td><td class="company">Brightpath Corp.</td><td><div class="add">Add</div></td></tr>
      </tbody>
    </table>
    <div class="pager">
      <div class="pg-btn">‹ Back</div>
      <div class="pg-num current">1</div>
      <div class="pg-num">2</div>
      <div class="pg-btn">Next ›</div>
    </div>
  </div>
</div>
</body>
</html>
```